Business Card Design

I already have a company logo for my company. I have a logo for the manufacturer we represent. I want a professional business card design.

```html
<!DOCTYPE html>
<html lang="en">
<head>
<meta charset="utf-8">
<title>Signal Guard LLC – Business Card</title>
<link href="https://fonts.googleapis.com/css2?family=Montserrat:wght@400;500;700;800&display=swap" rel="stylesheet">
<style>
  :root {
    --backdrop: #e9e7e4;
    --card-black: #1b1b1d;
    --card-black-soft: #2a2a2d;
    --card-white: #ffffff;
    --accent-red: #e2363f;
    --accent-gold: #c9a227;
    --logo-grey: #8d8f93;
    --text-light: #e6e6e6;
  }
  * { box-sizing: border-box; margin: 0; padding: 0; }
  html, body {
    width: 1200px; height: 913px; overflow: hidden;
    background: var(--backdrop);
    font-family: "Montserrat", sans-serif;
  }
  .canvas {
    position: relative; width: 1200px; height: 913px;
  }
  .card {
    position: absolute; top: 306px;
    width: 525px; height: 300px;
    border-radius: 4px;
    overflow: hidden;
    box-shadow: 0 10px 24px rgba(0,0,0,.22);
  }
  /* Front */
  .card-front {
    left: 60px;
    background: linear-gradient(135deg, var(--card-black-soft), var(--card-black) 70%);
    display: flex; align-items: center; justify-content: center;
  }
  .brand {
    display: flex; align-items: center; gap: 12px;
  }
  .brand-mark {
    width: 18px; height: 18px; background: var(--accent-gold);
  }
  .brand-name {
    font-weight: 800; font-size: 34px; letter-spacing: 1px;
    text-transform: uppercase; line-height: 1;
  }
  .card-front .brand-name { color: var(--logo-grey); }
  /* Back */
  .card-back {
    left: 615px;
    background: var(--card-white);
  }
  .back-top {
    position: absolute; left: 0; top: 0; width: 100%; height: 188px;
    display: flex; align-items: center; justify-content: center;
  }
  .card-back .brand-name { color: var(--accent-red); font-size: 32px; }
  .back-rule {
    position: absolute; left: 0; top: 188px; width: 100%; height: 3px;
    background: var(--accent-red);
  }
  .back-bottom {
    position: absolute; left: 0; top: 191px; width: 100%; height: 109px;
    background: var(--card-black);
    display: flex; align-items: center;
    padding: 0 28px 0 44px;
  }
  .person { width: 210px; }
  .person-name {
    color: var(--accent-red); font-weight: 700; font-size: 20px; line-height: 1.2;
  }
  .person-title {
    color: var(--text-light); font-weight: 400; font-size: 13px; margin-top: 2px;
  }
  .divider {
    width: 1px; height: 64px; background: var(--accent-red); margin-right: 18px;
  }
  .contact-list { list-style: none; }
  .contact-item {
    display: flex; align-items: center; gap: 10px;
    color: var(--text-light); font-size: 12.5px; line-height: 22px;
  }
  .contact-icon { width: 12px; height: 12px; flex: none; }
</style>
</head>
<body>
<main class="canvas">
  <section class="card card-front" aria-label="Card front">
    <div class="brand">
      <span class="brand-mark"></span>
      <span class="brand-name">Signal Guard LLC</span>
    </div>
  </section>

  <section class="card card-back" aria-label="Card back">
    <div class="back-top">
      <div class="brand">
        <span class="brand-mark"></span>
        <span class="brand-name">Signal Guard LLC</span>
      </div>
    </div>
    <div class="back-rule"></div>
    <div class="back-bottom">
      <div class="person">
        <p class="person-name">Dale Mercer</p>
        <p class="person-title">Managing Director</p>
      </div>
      <div class="divider"></div>
      <ul class="contact-list">
        <li class="contact-item">
          <svg class="contact-icon" viewBox="0 0 12 12" aria-hidden="true"><path d="M2.5 1h2l1 2.5-1.3 1a6 6 0 0 0 3.3 3.3l1-1.3L11 7.5v2a1 1 0 0 1-1 1A9 9 0 0 1 1.5 2a1 1 0 0 1 1-1z" fill="var(--accent-red)"/></svg>
          555.210.0147
        </li>
        <li class="contact-item">
          <svg class="contact-icon" viewBox="0 0 12 12" aria-hidden="true"><rect x="1" y="2.5" width="10" height="7" rx="1" fill="var(--accent-red)"/><path d="M1.5 3.2 6 6.6l4.5-3.4" stroke="var(--card-black)" stroke-width="1" fill="none"/></svg>
          info@signalguardco.com
        </li>
        <li class="contact-item">
          <svg class="contact-icon" viewBox="0 0 12 12" aria-hidden="true"><circle cx="6" cy="6" r="5" fill="none" stroke="var(--accent-red)" stroke-width="1.2"/><ellipse cx="6" cy="6" rx="2" ry="5" fill="none" stroke="var(--accent-red)" stroke-width="1"/><path d="M1 6h10" stroke="var(--accent-red)" stroke-width="1"/></svg>
          www.signalguardco.com
        </li>
      </ul>
    </div>
  </section>
</main>
</body>
</html>
```